Veltrano.co - Polar Expeditions Specialists

We need a modern, visually striking business card for Veltrano.co, a company specialized in selling expedition cruises to the most remote regions on Earth, with a focus on the Arctic and Antarctica. The design should instantly communicate that the cardholder is an expert in polar travel. Use clean, premium aesthetics with cool tones like icy blue and white, possibly incorporating polar imagery (ice, glaciers, penguins, etc.)

Attached the logo

Contact Information for Business Card

Feels high-end and trustworthy.. Visually memorable — encourages people to keep it

Colors
0054AA
0677BA
7BADD7
CADEEF
E8F1F8

Requirements
Must have
• ice, glaciers, penguins, montains
Nice to have
• modern, transparente,

```html
<!DOCTYPE html>
<html lang="en">
<head>
<meta charset="utf-8">
<title>Veltrano.co Business Card</title>
<link href="https://fonts.googleapis.com/css2?family=Poppins:wght@500;600;700&family=Montserrat:wght@400;500&display=swap" rel="stylesheet">
<style>
  :root {
    --page-bg: #e4e4e6;
    --card-white: #ffffff;
    --brand-blue: #3a6db5;
    --band-blue: #3577b8;
    --back-blue: #3677b7;
    --deep-blue: #0b55a5;
    --ink: #1c1c1c;
    --white: #ffffff;
  }
  * { margin: 0; padding: 0; box-sizing: border-box; }
  html, body { width: 1200px; height: 1108px; overflow: hidden; }
  body { background: var(--page-bg); position: relative; font-family: "Montserrat", sans-serif; }

  .card { position: absolute; overflow: hidden; }
  .card-front { left: 219px; top: 50px; width: 774px; height: 473px; background: var(--card-white); }
  .card-back { left: 217px; top: 568px; width: 776px; height: 457px; background: var(--back-blue); }

  .brand { position: absolute; left: 100px; top: 203px; width: 282px; text-align: center; }
  .brand-name { font-family: "Poppins", sans-serif; font-weight: 700; font-size: 44px; line-height: 1; color: var(--brand-blue); white-space: nowrap; }
  .brand-tagline { font-family: "Poppins", sans-serif; font-weight: 600; font-size: 15px; color: var(--brand-blue); margin-top: 10px; white-space: nowrap; }

  .divider { position: absolute; left: 397px; top: 165px; width: 2px; height: 150px; background: var(--brand-blue); }

  .person { position: absolute; left: 410px; top: 160px; }
  .person-name { font-family: "Poppins", sans-serif; font-weight: 600; font-size: 28px; line-height: 1.1; color: var(--brand-blue); white-space: nowrap; }
  .person-title { font-size: 18px; color: var(--ink); margin-top: 3px; white-space: nowrap; }

  .contacts { list-style: none; margin-top: 12px; }
  .contacts li { display: flex; align-items: center; height: 30px; font-size: 18px; color: var(--ink); white-space: nowrap; }
  .contacts svg { width: 16px; height: 16px; margin-right: 10px; fill: var(--brand-blue); flex: none; }

  .address-band { position: absolute; left: 0; top: 388px; width: 100%; height: 50px; background: var(--band-blue); color: var(--white); font-size: 18px; display: flex; align-items: center; justify-content: center; }

  .back-brand { position: absolute; left: 110px; top: 178px; display: flex; align-items: center; }
  .back-mark { width: 110px; height: 110px; border-radius: 50%; background: var(--deep-blue); margin-right: 42px; }
  .back-name { font-family: "Poppins", sans-serif; font-weight: 700; font-size: 66px; line-height: 1; color: var(--deep-blue); white-space: nowrap; }
  .back-tagline { font-family: "Poppins", sans-serif; font-weight: 600; font-size: 22px; color: var(--deep-blue); margin-top: 10px; white-space: nowrap; }
</style>
</head>
<body>
  <section class="card card-front">
    <div class="brand">
      <div class="brand-name">Veltrano.co</div>
      <div class="brand-tagline">Polar Expeditions Specialists</div>
    </div>
    <div class="divider"></div>
    <div class="person">
      <div class="person-name">Marcus Elwood</div>
      <div class="person-title">Managing Director</div>
      <ul class="contacts">
        <li>
          <svg viewBox="0 0 24 24" aria-hidden="true"><path d="M6.6 10.8a15.1 15.1 0 0 0 6.6 6.6l2.2-2.2a1 1 0 0 1 1-.25 11.4 11.4 0 0 0 3.6.57 1 1 0 0 1 1 1V20a1 1 0 0 1-1 1A17 17 0 0 1 3 4a1 1 0 0 1 1-1h3.5a1 1 0 0 1 1 1c0 1.25.2 2.45.57 3.6a1 1 0 0 1-.25 1z"/></svg>
          (555)014-2270
        </li>
        <li>
          <svg viewBox="0 0 24 24" aria-hidden="true"><path d="M3 5h18v2.2l-9 5.6-9-5.6zM3 9.5l9 5.6 9-5.6V19H3z"/></svg>
          info@veltrano.co
        </li>
        <li>
          <svg viewBox="0 0 24 24" aria-hidden="true"><path d="M12 2a10 10 0 1 0 0 20 10 10 0 0 0 0-20zm-1 17.9A8 8 0 0 1 4.1 10.6L9 15.5v1a2 2 0 0 0 2 2zm6.9-2.5A2 2 0 0 0 16 16h-1v-3a1 1 0 0 0-1-1H8v-2h2a1 1 0 0 0 1-1V7h2a2 2 0 0 0 2-2v-.4a8 8 0 0 1 2.9 12.8z"/></svg>
          www.veltrano.co
        </li>
      </ul>
    </div>
    <div class="address-band">48 Harbor Point Avenue Easton, CT 06612 USA</div>
  </section>

  <section class="card card-back">
    <div class="back-brand">
      <div class="back-mark"></div>
      <div>
        <div class="back-name">Veltrano.co</div>
        <div class="back-tagline">Polar Expeditions Specialists</div>
      </div>
    </div>
  </section>
</body>
</html>
```